Business Card Design

WE are looking for a premium quality Business Cards for a Law Firm . Copies of our current business card is attached.

Contact Information for Business Card

xyz

```html
<!DOCTYPE html>
<html lang="en">
<head>
<meta charset="utf-8">
<title>Harlow Lawyers – Business Cards</title>
<link href="https://fonts.googleapis.com/css2?family=Cinzel:wght@600;700&family=Arimo:wght@400;700&display=swap" rel="stylesheet">
<style>
  :root {
    --backdrop: #3a332f;
    --green: #0f3323;
    --green-deep: #0a2a1c;
    --gold: #b8935a;
    --white: #ffffff;
    --paper: #f7f7f5;
  }
  * { box-sizing: border-box; margin: 0; padding: 0; }
  html, body { width: 1200px; height: 716px; overflow: hidden; }
  body {
    background: var(--backdrop);
    font-family: "Arimo", Arial, sans-serif;
    position: relative;
  }
  .card {
    position: absolute;
    width: 520px;
    height: 318px;
    top: 199px;
    overflow: hidden;
    box-shadow: 0 10px 24px rgba(0,0,0,.45);
  }
  .card-front { left: 50px; }
  .card-back { left: 630px; background: var(--green); }

  .front-shape { position: absolute; inset: 0; }

  .brand {
    position: absolute;
    text-align: center;
    font-family: "Cinzel", Georgia, serif;
    font-weight: 700;
    line-height: 1;
  }
  .brand-mark {
    display: block;
    margin: 0 auto 10px;
    border-radius: 50%;
  }
  .brand-name { display: block; }
  .brand-sub { display: block; letter-spacing: .45em; }

  .front-brand { left: 18px; top: 92px; width: 190px; color: var(--green); }
  .front-brand .brand-mark { width: 52px; height: 52px; border: 3px solid var(--gold); }
  .front-brand .brand-name { font-size: 30px; }
  .front-brand .brand-sub { font-size: 13px; margin-top: 6px; }

  .person {
    position: absolute;
    right: 30px;
    top: 38px;
    text-align: right;
    color: var(--white);
  }
  .person-name {
    font-family: "Cinzel", Georgia, serif;
    font-weight: 700;
    color: var(--gold);
    font-size: 19px;
    letter-spacing: .02em;
  }
  .person-role { font-size: 12.5px; line-height: 1.3; margin-top: 3px; }

  .address {
    position: absolute;
    right: 30px;
    top: 128px;
    text-align: right;
    color: var(--white);
    font-size: 13px;
    line-height: 1.35;
    font-style: normal;
  }
  .contacts {
    position: absolute;
    right: 30px;
    top: 200px;
    list-style: none;
    color: var(--white);
    font-size: 13px;
    line-height: 1.35;
  }
  .contacts li { display: flex; justify-content: flex-end; align-items: center; gap: 8px; }
  .contacts svg { width: 11px; height: 11px; fill: var(--gold); flex: none; }

  .back-brand { left: 210px; top: 54px; width: 250px; color: var(--white); }
  .back-brand .brand-mark { width: 64px; height: 64px; border: 3px solid var(--white); }
  .back-brand .brand-name { font-size: 40px; }
  .back-brand .brand-sub { font-size: 15px; margin-top: 8px; }

  .offices {
    position: absolute;
    left: 18px;
    right: 18px;
    bottom: 28px;
    display: grid;
    grid-template-columns: 1fr 1fr 1fr;
    color: var(--white);
    font-size: 11px;
    line-height: 1.35;
    text-align: center;
  }
  .office { padding: 0 8px; }
  .office + .office { border-left: 1px solid rgba(255,255,255,.7); }
  .office-city { font-weight: 700; font-size: 13px; margin-bottom: 2px; }
  .office-phone b { font-weight: 700; }
</style>
</head>
<body>

<section class="card card-front" aria-label="Business card front">
  <svg class="front-shape" viewBox="0 0 520 318" preserveAspectRatio="none" aria-hidden="true">
    <rect width="520" height="318" fill="var(--green-deep)"/>
    <path d="M0 0 H228 C292 95 280 258 160 318 H0 Z" fill="var(--gold)"/>
    <path d="M0 0 H214 C272 92 262 252 150 318 H0 Z" fill="var(--paper)"/>
  </svg>

  <div class="brand front-brand">
    <span class="brand-mark"></span>
    <span class="brand-name">HARLOW</span>
    <span class="brand-sub">LAWYERS</span>
  </div>

  <div class="person">
    <h1 class="person-name">DANIEL MERCER</h1>
    <p class="person-role">Director &amp; Principal Solicitor<br>MBA, Juris Doctor</p>
  </div>

  <address class="address">
    Level 4, Harlow Chambers<br>
    210 Ferncourt Road<br>
    Spring Hill, QLD 4010
  </address>

  <ul class="contacts">
    <li>+61 7 3000 4812
      <svg viewBox="0 0 24 24" aria-label="Phone"><path d="M6.6 10.8a15 15 0 0 0 6.6 6.6l2.2-2.2c.3-.3.7-.4 1-.2 1.1.4 2.3.6 3.6.6.6 0 1 .4 1 1V20c0 .6-.4 1-1 1C10.6 21 3 13.4 3 4c0-.6.4-1 1-1h3.5c.6 0 1 .4 1 1 0 1.3.2 2.5.6 3.6.1.3 0 .7-.2 1z"/></svg>
    </li>
    <li>+61 0400 117 362
      <svg viewBox="0 0 24 24" aria-label="Mobile"><path d="M7 1h10a2 2 0 0 1 2 2v18a2 2 0 0 1-2 2H7a2 2 0 0 1-2-2V3a2 2 0 0 1 2-2zm0 3v14h10V4zm5 15.5a1 1 0 1 0 0 2 1 1 0 0 0 0-2z"/></svg>
    </li>
    <li>daniel@harlowlawyers.com.au
      <svg viewBox="0 0 24 24" aria-label="Email"><path d="M2 5h20v14H2zm2 2v.5l8 5 8-5V7zm0 3v7h16v-7l-8 5z"/></svg>
    </li>
    <li>www.harlowlawyers.com.au
      <svg viewBox="0 0 24 24" aria-label="Website"><path d="M12 2a10 10 0 1 0 0 20 10 10 0 0 0 0-20zm0 2c1 0 2.3 2 2.8 5H9.2C9.7 6 11 4 12 4zm-7.7 7h3.8a17 17 0 0 0 0 2H4.3a8 8 0 0 1 0-2zm5.8 0h3.8a15 15 0 0 1 0 2h-3.8a15 15 0 0 1 0-2zm5.8 0h3.8a8 8 0 0 1 0 2h-3.8a17 17 0 0 0 0-2zM9.2 15h5.6c-.5 3-1.8 5-2.8 5s-2.3-2-2.8-5z"/></svg>
    </li>
  </ul>
</section>

<section class="card card-back" aria-label="Business card back">
  <div class="brand back-brand">
    <span class="brand-mark"></span>
    <span class="brand-name">HARLOW</span>
    <span class="brand-sub">LAWYERS</span>
  </div>

  <div class="offices">
    <div class="office">
      <p class="office-city">Melbourne</p>
      <p>Level 22, 48 Ashgrove Street<br>Melbourne, VIC 3001</p>
      <p class="office-phone"><b>Phone :</b> +61 03 9000 3318</p>
    </div>
    <div class="office">
      <p class="office-city">Sydney</p>
      <p>Level 12, Corbel House<br>75 Linden Street<br>Parramatta, NSW 2151</p>
      <p class="office-phone"><b>Phone :</b> +61 02 9000 7724</p>
    </div>
    <div class="office">
      <p class="office-city">Perth</p>
      <p>Level 19, Kestrel Tower<br>92 Marlow Terrace<br>Perth, WA 6001</p>
      <p class="office-phone"><b>Phone :</b> +61 08 6000 5930</p>
    </div>
  </div>
</section>

</body>
</html>
```